Flyer Vacation Gift Certificate

I need to create a beautiful flyer 8.5 x 11 PDF format flyer design. <br/><br/>Instructions:<br/>The flyer will really be a gift voucher for a las vegas vacation getaway. So must have a Las Vegas Theme exciting fun<br/><br/>The voucher should have two modules that will be editable. <br/>Must have a "Compliments Of" area and also must have an "Exclusively For" area<br/><br/>Keep in mind that this flyer will be printed so keep that in mind :)<br/><br/>Here the is the content for the vacation voucher:<br/><br/>There is no doubt that Las Vegas is one of the hottest travel destinations around the world. In fact, some people would even go as far as<br/>saying that perhaps it is THE hottest place to visit. Enjoy up to 4 nights of resort/casino accommodations in exciting Las Vegas, NV. Millions of people travel to this exciting city each year to enjoy its thrills. Thanks to the business you received this certificate from, now you can enjoy exciting Las Vegas, NV too!<br/><br/>Features:<br/>*Travel 7 Days A Week<br/>*Stay Your Choice Of Nights (1-4 Nights)<br/>*Good For Two Adults & Two Children<br/>*Pay Just The Taxes & Fees<br/>*Multiple Travel Date Requests Allowed<br/>*Fully Transferable To Another Person<br/>*Just A 30 Days Advance Notice Required<br/>*You Will Have 12 Months To Complete Travel After Redemption<br/><br/>HOW CAN WE DO THIS?<br/><br/>We contract with the world leading hotel chains and resorts to help them fill their otherwise empty rooms.<br/><br/>We help fill empty rooms which the hotels, resorts and cruise lines turn into additional revenue from other areas of their property and future bookings.<br/><br/>Hotels rarely experience full occupancy, yet they remain open, providing rooms and services at fixed costs. So when hotels give out their rooms by partnering with marketing companies like us, they might miss out on the room fee, but they already didn't have that in the first place, at least now they have the opportunity to gain a customer for their in-house restaurants, room service, their casinos, an extra day stay, future bookings, etc.<br/><br/>VIEW ALL THE DETAILS OF THIS SPECIAL OFFER AND REDEEM ONLINE AT <br/>WWW.QOTAVERNIX.COM<br/><br/>Certificate ID # 47261-38157<br/>Expires 02/29/2020<br/><br/><br/>*terms and conditions apply see website for details<br/><br/>KEEP IN MIND THE EXAMPLES I AM UPLOADING ARE SIMPLY TO SHOW YOU THAT THEY CONTAIN THE "COMPLIMENTS OF" AND "EXCLUSIVELY FOR" ELEMENTS. THESE MUST BE INCLUDED IN NEW DESIGN. PLEASE ONLY USE THE CONTENT I PROVIDED IN BRIEF, DONT USE CONTENT FROM EXAMPLES.

Target Market(s)

CONSUMERS THAT HAVE BEEN REWARDED WITH A VACATION CERTIFICATE FOR DOING BUSINESS WITH A COMPANY.

COMPANIES USE THESE AS MARKETING INCENTIVES TO ATTRACT MORE CUSTOMERS AND TO REWARD LOYALTY, ETC.

Industry/Entity Type

Travel Industry

Colors

Designer to choose colors to be used in the design.

Requirements
Must have
• I need to create a beautiful flyer 8.5 x 11 PDF format flyer design.
• Instructions:
• The flyer will really be a gift voucher for a las vegas vacation getaway. So must have a Las Vegas Theme exciting fun
• The voucher should have two modules that will be editable.
• Must have a "Compliments Of" area and also must have an "Exclusively For" area
• Keep in mind that this flyer will be printed so keep that in mind :)
• Here the is the content for the vacation voucher:
• There is no doubt that Las Vegas is one of the hottest travel destinations around the world. In fact, some people would even go as far as
• saying that perhaps it is THE hottest place to visit. Enjoy up to 4 nights of resort/casino accommodations in exciting Las Vegas, NV. Millions of people travel to this exciting city each year to enjoy its thrills. Thanks to the business you received this certificate from, now you can enjoy exciting Las Vegas, NV too!
• Features:
• *Travel 7 Days A Week
• *Stay Your Choice Of Nights (1-4 Nights)
• *Good For Two Adults & Two Children
• *Pay Just The Taxes & Fees
• *Multiple Travel Date Requests Allowed
• *Fully Transferable To Another Person
• *Just A 30 Days Advance Notice Required
• *You Will Have 12 Months To Complete Travel After Redemption
• HOW CAN WE DO THIS?
• We contract with the world leading hotel chains and resorts to help them fill their otherwise empty rooms.
• We help fill empty rooms which the hotels, resorts and cruise lines turn into additional revenue from other areas of their property and future bookings.
• Hotels rarely experience full occupancy, yet they remain open, providing rooms and services at fixed costs. So when hotels give out their rooms by partnering with marketing companies like us, they might miss out on the room fee, but they already didn't have that in the first place, at least now they have the opportunity to gain a customer for their in-house restaurants, room service, their casinos, an extra day stay, future bookings, etc.
• VIEW ALL THE DETAILS OF THIS SPECIAL OFFER AND REDEEM ONLINE AT
• WWW.QOTAVERNIX.COM
• Certificate ID # 47261-38157
• Expires 02/29/2020
• *terms and conditions apply see website for details
• KEEP IN MIND THE EXAMPLES I AM UPLOADING ARE SIMPLY TO SHOW YOU THAT THEY CONTAIN THE "COMPLIMENTS OF" AND "EXCLUSIVELY FOR" ELEMENTS. THESE MUST BE INCLUDED IN NEW DESIGN. PLEASE ONLY USE THE CONTENT I PROVIDED IN BRIEF, DONT USE CONTENT FROM EXAMPLES.
Nice to have
• EXCITING LAS VEGAS IMAGES THAT MAKE SOMEONE WANT TO GO THERE

```html
<!DOCTYPE html>
<html lang="en">
<head>
<meta charset="utf-8">
<title>Las Vegas Vacation Certificate</title>
<link href="https://fonts.googleapis.com/css2?family=Roboto:ital,wght@0,400;0,500;0,700;0,900;1,900&family=Bebas+Neue&family=Roboto+Condensed:wght@400;700&display=swap" rel="stylesheet">
<style>
  :root {
    --ink: #111;
    --white: #fff;
    --red: #e0262a;
    --green: #1d5c48;
    --orange: #f7941d;
    --gold-top: #7c6237;
    --gold-mid: #c4aa72;
    --gold-low: #9a7c47;
    --frame: #8c7440;
    --navy: #0c0c1c;
  }
  * { box-sizing: border-box; margin: 0; padding: 0; }
  html, body { width: 927px; height: 1200px; overflow: hidden; background: var(--white); }
  body { font-family: 'Roboto', sans-serif; color: var(--ink); }
  .flyer { position: relative; width: 927px; height: 1200px; overflow: hidden; background: var(--white); }

  .hero {
    position: absolute; left: 0; top: 0; width: 927px; height: 436px;
    background:
      radial-gradient(ellipse 220px 70px at 700px 360px, rgba(40,90,190,0.95) 0%, rgba(30,60,140,0.6) 55%, rgba(30,60,140,0) 100%),
      radial-gradient(ellipse 260px 80px at 430px 300px, rgba(255,196,90,0.75) 0%, rgba(230,130,60,0.35) 50%, rgba(230,130,60,0) 100%),
      radial-gradient(ellipse 120px 150px at 140px 230px, rgba(236,90,170,0.55) 0%, rgba(236,90,170,0) 100%),
      radial-gradient(ellipse 200px 70px at 820px 300px, rgba(255,190,80,0.55) 0%, rgba(255,190,80,0) 100%),
      linear-gradient(180deg, #1f6fc8 0%, #5c9bd8 14%, #8fb6d8 22%, #3c5a8c 32%, #2b3556 46%, #5a4058 60%, #b37a3e 74%, #3b4a36 86%, #1d2a45 100%);
  }
  .compliments {
    position: absolute; left: 645px; top: 51px; width: 231px; height: 231px;
    background: var(--white); text-align: center;
  }
  .compliments-title {
    margin-top: 25px; font-weight: 700;
    font-size: 18.5px; line-height: 19.5px; color: var(--green);
  }
  .compliments-lines {
    position: absolute; left: 0; right: 0; top: 157px;
    font-weight: 500; font-size: 17.5px; line-height: 19.8px;
  }
  .exclusive {
    position: absolute; left: 0; top: 350px; width: 357px; height: 35px;
    background: var(--red); color: var(--white);
    font-weight: 700; font-size: 17px;
    line-height: 35px; padding-left: 36px; white-space: nowrap;
  }

  .photo {
    position: absolute; top: 400px; width: 269px; height: 205px;
    border: 4px solid var(--frame);
    box-shadow: 0 10px 8px -6px rgba(0,0,0,0.45);
  }
  .photo-sign {
    left: 42px;
    background:
      radial-gradient(ellipse 80px 45px at 50% 40%, rgba(255,240,230,0.9) 0%, rgba(230,60,80,0.7) 45%, rgba(120,40,150,0) 100%),
      radial-gradient(ellipse 140px 90px at 50% 30%, rgba(150,60,190,0.6) 0%, rgba(150,60,190,0) 100%),
      linear-gradient(180deg, #07070e 0%, #120a18 55%, #4a3a22 85%, #1a1410 100%);
  }
  .photo-hotel {
    left: 331px;
    background:
      radial-gradient(ellipse 70px 45px at 30% 78%, rgba(255,150,90,0.95) 0%, rgba(240,90,60,0.6) 50%, rgba(240,90,60,0) 100%),
      radial-gradient(ellipse 110px 70px at 62% 40%, rgba(230,232,240,0.85) 0%, rgba(180,185,205,0.4) 55%, rgba(180,185,205,0) 100%),
      linear-gradient(180deg, #12162a 0%, #2a3050 40%, #6a3a3a 80%, #1c1214 100%);
  }
  .photo-strip {
    left: 617px;
    background:
      radial-gradient(ellipse 70px 40px at 48% 85%, rgba(255,90,70,0.9) 0%, rgba(255,90,70,0) 100%),
      radial-gradient(ellipse 60px 90px at 85% 55%, rgba(240,80,170,0.6) 0%, rgba(240,80,170,0) 100%),
      radial-gradient(ellipse 40px 70px at 58% 30%, rgba(255,180,60,0.7) 0%, rgba(255,180,60,0) 100%),
      linear-gradient(180deg, #0b0c18 0%, #1a1c30 40%, #3a2a2a 70%, #2a1a14 100%);
  }

  .heading {
    position: absolute; left: 37px; font-family: 'Bebas Neue', sans-serif;
    font-size: 36px; line-height: 1; color: var(--ink);
  }
  .features-heading { top: 652px; }
  .how-heading { top: 831px; }
  .features {
    position: absolute; left: 38px; top: 689px; list-style: none;
    font-size: 12.2px; line-height: 15.2px;
  }
  .features li { position: relative; padding-left: 20px; }
  .features li::before {
    content: ""; position: absolute; left: 1px; top: 2.5px; width: 10px; height: 10px;
    border: 1.5px solid var(--orange); background: var(--white);
    box-shadow: inset 0 0 0 1.5px var(--white), inset 0 0 0 5px var(--orange);
  }
  .points { position: absolute; left: 37px; top: 872px; width: 481px; list-style: none; }
  .points li {
    position: relative; padding-left: 28px; font-size: 12.2px; line-height: 12.1px;
    margin-bottom: 9.5px;
  }
  .points svg { position: absolute; left: 0; top: 0; }
  .redeem {
    position: absolute; left: 36px; top: 1029px; font-weight: 900; font-style: italic;
    font-size: 18px; line-height: 18.5px; white-space: nowrap;
  }
  .contact-heading {
    position: absolute; left: 39px; top: 1090px; font-family: 'Bebas Neue', sans-serif;
    font-size: 29px; line-height: 27px; border-bottom: 2px solid var(--ink);
  }
  .contacts { position: absolute; left: 39px; top: 1131px; font-size: 14px; line-height: 20px; }
  .contacts span { position: absolute; white-space: nowrap; }
  .contacts b { color: var(--orange); font-weight: 500; }

  .blurb-panel {
    position: absolute; left: 525px; top: 632px; width: 351px; height: 502px;
    background: linear-gradient(180deg, var(--gold-top) 0%, var(--gold-mid) 55%, var(--gold-low) 100%);
  }
  .blurb {
    position: absolute; left: 0; right: 0; top: 23px; padding: 0 24px; text-align: center;
    color: var(--white); font-weight: 500;
    font-size: 18.6px; line-height: 24.2px;
  }
  .cert-box {
    position: absolute; left: 42px; top: 408px; width: 266px; height: 68px;
    background: var(--white); text-align: center; color: var(--ink);
    padding-top: 5px;
  }
  .cert-box p { font-weight: 500; font-size: 16.5px; line-height: 19.5px; white-space: nowrap; }
  .cert-box small {
    display: block; font-family: 'Roboto Condensed', sans-serif; font-weight: 400;
    font-size: 11px; line-height: 17px; letter-spacing: -0.2px; white-space: nowrap;
  }

  .footer-band { position: absolute; left: 0; top: 0; }
  .footer-site {
    position: absolute; left: 525px; top: 1137px; width: 351px; text-align: center;
    color: var(--white); font-weight: 700; font-size: 33px; line-height: 40px;
  }
</style>
</head>
<body>
<main class="flyer">
  <div class="hero" role="img" aria-label="Aerial evening view of the Las Vegas Strip with lit casino towers, a tower replica and the fountain lake"></div>

  <section class="compliments">
    <h2 class="compliments-title">THIS CERTIFICATE IS<br>COMPLIMENTS OF</h2>
    <p class="compliments-lines">Certificate Courtesy Of<br>Text Line 2<br>Text Line 3</p>
  </section>

  <div class="exclusive">EXCLUSIVELY FOR : CUSTOMER NAME</div>

  <div class="photo photo-sign" role="img" aria-label="Welcome to Las Vegas roadside sign glowing at night between palm trees"></div>
  <div class="photo photo-hotel" role="img" aria-label="White casino hotel tower lit at night above a glowing neon flower facade"></div>
  <div class="photo photo-strip" role="img" aria-label="Busy Las Vegas boulevard at night with red traffic lights and neon signs"></div>

  <h2 class="heading features-heading">FEATURES:</h2>
  <ul class="features">
    <li>Travel 7 Days A Week</li>
    <li>Stay Your Choice Of Nights (1-4 Nights)</li>
    <li>Good For Two Adults &amp; Two Children</li>
    <li>Pay Just The Taxes &amp; Fees</li>
    <li>Multiple Travel Date Requests Allowed</li>
    <li>Fully Transferable To Another Person</li>
    <li>Just A 30 Days Advance Notice Required</li>
    <li>You Will Have 12 Months To Complete Travel After Redemption</li>
  </ul>

  <h2 class="heading how-heading">HOW CAN WE DO THIS?</h2>
  <ul class="points">
    <li><svg width="22" height="20" viewBox="0 0 22 20"><path d="M2 6h13M11 2l4 4-4 4M2 10v7h10" fill="none" stroke="#f7941d" stroke-width="1.6"/></svg>We contract with the world leading hotel chains and resorts to help them fill their otherwise empty rooms.</li>
    <li><svg width="22" height="20" viewBox="0 0 22 20"><path d="M2 6h13M11 2l4 4-4 4M2 10v7h10" fill="none" stroke="#f7941d" stroke-width="1.6"/></svg>We help fill empty rooms which the hotels, resorts and cruise lines turn into<br>additional revenue from other areas of their property and future bookings.</li>
    <li><svg width="22" height="20" viewBox="0 0 22 20"><path d="M2 6h13M11 2l4 4-4 4M2 10v7h10" fill="none" stroke="#f7941d" stroke-width="1.6"/></svg>Hotels rarely experience full occupancy, yet they remain open, providing rooms and services at fixed costs. So when hotels give out their rooms by partnering with marketing companies like us, they might miss out on the room fee, but they already didn't have that in the first place, at least now they have the opportunity to gain a customer for their in-house restaurants, room service, their casinos, an extra day stay, future bookings, etc.</li>
  </ul>

  <p class="redeem">VIEW ALL THE DETAILS OF THIS SPECIAL OFFER AND<br>REDEEM ONLINE AT WWW.QOTAVERNIX.COM</p>

  <h2 class="contact-heading">GET IN TUCH</h2>
  <div class="contacts">
    <span style="left:0;top:0"><b>Countact us</b>:www.Qotavernix.Com</span>
    <span style="left:234px;top:0"><b>Email</b>:Contact@Qotavernix.Com</span>
    <span style="left:0;top:20px"><b>Social</b>/Qotavernix</span>
    <span style="left:234px;top:20px"><b>Updates</b>/Qotavernix</span>
  </div>

  <section class="blurb-panel">
    <p class="blurb">There is no doubt that Las Vegas is one of the hottest travel destinations around the world. In fact, some people would even go as far as<br>saying that perhaps it is THE hottest place to visit. Enjoy up to 4 nights of resort/casino accommodations in exciting Las Vegas, NV. Millions of people travel to this exciting city each year to enjoy its thrills. Thanks to the business you received this certificate from, now you can enjoy exciting Las Vegas, NV too!</p>
    <div class="cert-box">
      <p>CERTIFICATE ID # 47261-38157<br>EXPIRES 02/29/2020</p>
      <small>(Terms and conditions apply see website for details)</small>
    </div>
  </section>

  <svg class="footer-band" width="927" height="1200" viewBox="0 0 927 1200" aria-hidden="true">
    <polygon points="451,1200 525,1133 927,1133 927,1200" fill="#0c0c1c"/>
  </svg>
  <div class="footer-site">QOTAVERNIX.COM</div>
</main>
</body>
</html>
```